Modern Can & Tray Design Competition

Please note our brand is now called ké, please do not submit any entries with the wording or logo of "ké pulpwell". Read the full design brief below before making an entry, please.

A competition to design can packaging and outer tray designs for a new exciting brand.

See examples of the design assets I want, below, including both a can and outer tray:

1. https://grazmoortraders-zeeland.eu/beverages/energy-drinks/volt-hare-energy-the-green-edition-12-x-025-liter-cans-nl/?lang=en

2. https://www.vimp.com/nl/nl/p/zinta-fizz-cherry-slim-cans-24-x-330-ml-eu/4711000052938461/

We have 2 flavours in our range, so we need two separate can designs and a separate outer tray design for each flavour.

Our drinks are currently packaged in PET plastic bottles. Our flavours are:
Lemon & Lime - https://kepulpwell.co.uk/products/lemon-and-lime
Strawberry - https://kepulpwell.co.uk/products/strawberry

For this competition, I want can designs for each flavour in 250ml style cans like used by Volthare. And I also want an outer tray for the cans designed for each flavour. Our brand is changing to “ké” so please do not use “pulpwell” on any part of the design. The logo should be “ké” and for each flavour the ke should show the fruit for the flavour embedded inside it. See the files called “ke_fruit_logo_LEMLI (1)” and “ke_fruit_logo_STR (1)” for what I mean. You can use these files for your design.

Under the logo it should state on the can “Prebiotic Fibre Drink”. Similar to how VoltHare has “Energy Drink” written under its logo: https://www.lumo-vesta.com/wp-content/uploads/2009/11/volt-hare-can-250ml-1.jpg

If you can submit your design ideas for this competition with a picture of the can next to the tray like this for each flavour, that will be best: https://m.media-quillmart.com/images/I/47kTxPq2Lw8._SL1500_.jpg

So, two design concepts/ideas are needed to enter: One for Lemon & Lime and one for Strawberry.

We want vibrant, eye-catching packaging designs that will catch the consumer's attention.

Right now, we have ke in the centre of our packaging design with fruit embedded in the ke. This must remain a key part of your design as mentioned above. Also, as we will be launching other drinks as a company under different brand names and to unify our different brands we want a splash effect on all the cans which will be replicated across our other brands. So, please have some kind of splash effect on each flavour that can be replicated on the cans of our other brands in future.

Design considerations:

There is also certain information we need on the front/face of the can.

On the very top of the can just below the neck and above the logo we want it to state: “Supports Gut & Overall health*” example: https://pkrprovisions.co.uk/wp-content/uploads/2023/10/Zest-Bloom-Lemonade.jpg

We also want the number of calories to be stated somewhere on the can in a clever way like in a droplet of the water splash effect. The number of the calories is “17 kcals”.

Under the ke logo as mentioned we want the wording: “Prebiotic Fibre Drink”

Then under Prebiotic Fibre Drink we want the name of the flavour - and then under the flavour we want 3 features stated. Which are:

“20% of daily fibre”
“0g sugar”
“Nothing artificial“

This could be laid out as 3 circles with icons or some other way. The last piece of information under these 3 features is then the size of the can “250 mle”.

In terms of “feel” of the design we want a vibrant colourful feel, and it should show pictures of fruit on it. Here is an example
https://thehiddenorchardtales.com/wp-content/uploads/sites/2/2023/03/THOT-US-SodaRange-%E2%80%93-bb-1220x883.png

Any questions let me know. I look forward to seeing your ideas.

To see more about our brand, view our website: www.kepulpwell.co.uk

```html
<!DOCTYPE html>
<html lang="en">
<head>
<meta charset="utf-8">
<title>ke Lemon &amp; Lime — Can &amp; Tray</title>
<link href="https://fonts.googleapis.com/css2?family=Poppins:wght@400;500;600;700&display=swap" rel="stylesheet">
<style>
  :root {
    --bg: #ffffff;
    --lemon: #fcd316;
    --leaf: #4fa84a;
    --leaf-dark: #3f9140;
    --ink: #1d1d1b;
    --white: #ffffff;
    --citrus-light: #f7e27a;
    --citrus-mid: #e9c936;
    --lime-mid: #7dbb3c;
  }
  * { box-sizing: border-box; margin: 0; padding: 0; }
  html, body { width: 1125px; height: 1200px; overflow: hidden; background: var(--bg); }
  body { position: relative; font-family: "Poppins", sans-serif; color: var(--ink); }

  .panel { position: absolute; background: var(--lemon); overflow: hidden; box-shadow: 0 4px 14px rgba(0,0,0,0.12); }
  .caption { position: absolute; font-size: 30px; font-weight: 400; text-align: center; color: var(--ink); }

  /* Can label */
  .can-label { left: 416px; top: 40px; width: 292px; height: 734px; }
  .can-label .claim { position: absolute; top: 18px; left: 0; width: 100%; text-align: center; font-size: 16.5px; font-weight: 500; }
  .fruit-top { position: absolute; left: 10px; top: 78px; width: 235px; height: 120px; border-radius: 50% 50% 30% 30%;
    background: radial-gradient(ellipse at 30% 60%, var(--lime-mid) 0%, var(--citrus-light) 55%, var(--citrus-mid) 100%); opacity: .85; }
  .kcal-tab { position: absolute; background: var(--leaf); color: var(--white); display: flex; align-items: center; justify-content: center; font-size: 15px; }
  .can-label .kcal-tab { right: 0; top: 74px; width: 45px; height: 76px; border-radius: 8px 0 0 8px; }
  .kcal-tab span { writing-mode: vertical-rl; white-space: nowrap; }
  .tray .kcal-tab span { transform: rotate(180deg); }

  .badge { position: absolute; background: var(--white); border-radius: 50%; display: flex; flex-direction: column; align-items: center; justify-content: center; }
  .can-label .badge { left: 21px; top: 123px; width: 250px; height: 250px; }
  .brand-name { color: var(--ink); font-weight: 500; line-height: 1; letter-spacing: 1px; }
  .can-label .brand-name { font-size: 64px; }
  .descriptor { font-weight: 400; letter-spacing: .2px; color: var(--ink); }
  .can-label .descriptor { font-size: 14px; margin-top: 18px; }

  .can-label .flavour { position: absolute; left: 14px; top: 690px; transform-origin: 0 0; transform: rotate(-90deg);
    font-size: 48px; font-weight: 700; color: var(--leaf); white-space: nowrap; line-height: 1; }
  .fruit-cluster { position: absolute; border-radius: 46% 54% 40% 60%;
    background: radial-gradient(circle at 35% 55%, var(--citrus-light) 0%, var(--citrus-mid) 45%, var(--lime-mid) 80%, var(--leaf-dark) 100%); }
  .can-label .fruit-cluster { left: 66px; top: 405px; width: 226px; height: 200px; }

  .features { position: absolute; display: flex; }
  .feature { display: flex; flex-direction: column; align-items: center; text-align: center; }
  .feature svg { display: block; }
  .feature p { line-height: 1.05; margin-top: 4px; }
  .can-label .features { left: 84px; top: 612px; }
  .can-label .feature { width: 67px; }
  .can-label .feature p { font-size: 11.5px; }

  .volume-band { position: absolute; left: 0; bottom: 0; width: 100%; height: 46px; }
  .volume { position: absolute; bottom: 13px; left: 80px; right: 0; text-align: center; color: var(--white); font-size: 14px; }

  /* Tray */
  .tray { left: 33px; top: 862px; width: 1058px; height: 265px; }
  .tray .kcal-tab { left: 0; top: 13px; width: 35px; height: 72px; border-radius: 0 8px 8px 0; font-size: 13px; }
  .tray .fruit-top { left: 75px; top: 18px; width: 200px; height: 100px; }
  .tray .badge { left: 81px; top: 67px; width: 190px; height: 190px; }
  .tray .brand-name { font-size: 50px; }
  .tray .descriptor { font-size: 11px; margin-top: 14px; }
  .tray .claim { position: absolute; left: 290px; width: 496px; top: 32px; text-align: center; font-size: 24px; font-weight: 500; }
  .tray .flavour { position: absolute; left: 290px; width: 496px; top: 68px; text-align: center; font-size: 68px; font-weight: 700; color: var(--leaf); line-height: 1.1; }
  .tray .features { left: 445px; top: 165px; }
  .tray .feature { width: 62px; }
  .tray .feature p { font-size: 11.5px; }
  .tray .fruit-cluster { left: 790px; top: 42px; width: 268px; height: 200px; }
</style>
</head>
<body>

  <section class="panel can-label" aria-label="Can label">
    <p class="claim">Supports Gut &amp; Overall Health*</p>
    <div class="fruit-top" role="img" aria-label="Sliced lime and lemon halves with water splash"></div>
    <div class="kcal-tab"><span>17 kcals</span></div>
    <div class="badge">
      <p class="brand-name">ke</p>
      <p class="descriptor">PREBIOTIC FIBRE DRINK</p>
    </div>
    <div class="fruit-cluster" role="img" aria-label="Halved lemons and limes photo"></div>
    <h2 class="flavour">Lemon &amp; Lime</h2>
    <div class="features">
      <div class="feature">
        <svg width="40" height="40" viewBox="0 0 40 40"><circle cx="20" cy="20" r="18.5" fill="none" stroke="var(--leaf)" stroke-width="1.5"/><path d="M14 28 L24 16 L27 19 Z" fill="none" stroke="var(--leaf)" stroke-width="1.3"/><path d="M25 16 L28 11 M26 17 L31 14" stroke="var(--leaf)" stroke-width="1.3"/></svg>
        <p>20% of<br>daily fibre</p>
      </div>
      <div class="feature">
        <svg width="40" height="40" viewBox="0 0 40 40"><circle cx="20" cy="20" r="18.5" fill="none" stroke="var(--leaf)" stroke-width="1.5"/><path d="M20 11 L28 15 L28 25 L20 29 L12 25 L12 15 Z M12 15 L20 19 L28 15 M20 19 L20 29" fill="none" stroke="var(--leaf)" stroke-width="1.3"/></svg>
        <p>0g sugar</p>
      </div>
      <div class="feature">
        <svg width="40" height="40" viewBox="0 0 40 40"><circle cx="20" cy="20" r="18.5" fill="none" stroke="var(--leaf)" stroke-width="1.5"/><path d="M12 28 C12 18 18 12 29 11 C29 22 22 28 12 28 Z M12 28 L23 17" fill="none" stroke="var(--leaf)" stroke-width="1.3"/></svg>
        <p>Nothing<br>Artificial</p>
      </div>
    </div>
    <svg class="volume-band" viewBox="0 0 292 46" preserveAspectRatio="none"><path d="M0 36 L50 36 C70 36 72 0 100 0 L292 0 L292 46 L0 46 Z" fill="var(--leaf)"/></svg>
    <p class="volume">250 mle</p>
  </section>
  <p class="caption" style="left:416px; width:292px; top:784px;">Cane Design</p>

  <section class="panel tray" aria-label="Tray side panel">
    <div class="kcal-tab"><span>17 kcals</span></div>
    <div class="fruit-top" role="img" aria-label="Sliced lime and lemon halves with water splash"></div>
    <div class="badge">
      <p class="brand-name">ke</p>
      <p class="descriptor">PREBIOTIC FIBRE DRINK</p>
    </div>
    <p class="claim">Supports Gut &amp; Overall Health*</p>
    <h2 class="flavour">Lemon &amp; Lime</h2>
    <div class="features">
      <div class="feature">
        <svg width="38" height="38" viewBox="0 0 40 40"><circle cx="20" cy="20" r="18.5" fill="none" stroke="var(--leaf)" stroke-width="1.5"/><path d="M14 28 L24 16 L27 19 Z" fill="none" stroke="var(--leaf)" stroke-width="1.3"/><path d="M25 16 L28 11 M26 17 L31 14" stroke="var(--leaf)" stroke-width="1.3"/></svg>
        <p>20% of<br>daily fibre</p>
      </div>
      <div class="feature">
        <svg width="38" height="38" viewBox="0 0 40 40"><circle cx="20" cy="20" r="18.5" fill="none" stroke="var(--leaf)" stroke-width="1.5"/><path d="M20 11 L28 15 L28 25 L20 29 L12 25 L12 15 Z M12 15 L20 19 L28 15 M20 19 L20 29" fill="none" stroke="var(--leaf)" stroke-width="1.3"/></svg>
        <p>0g sugar</p>
      </div>
      <div class="feature">
        <svg width="38" height="38" viewBox="0 0 40 40"><circle cx="20" cy="20" r="18.5" fill="none" stroke="var(--leaf)" stroke-width="1.5"/><path d="M12 28 C12 18 18 12 29 11 C29 22 22 28 12 28 Z M12 28 L23 17" fill="none" stroke="var(--leaf)" stroke-width="1.3"/></svg>
        <p>Nothing<br>Artificial</p>
      </div>
    </div>
    <div class="fruit-cluster" role="img" aria-label="Halved lemons and limes photo"></div>
  </section>
  <p class="caption" style="left:33px; width:1058px; top:1140px;">Tray Design</p>

</body>
</html>
```